Brochure for people who suffer from Sleep Apnea and need a medical device called a CPAP Machine

I want a brochure that can be placed in doctors offices with my competitors brochures. It needs to be bold and stand out and deliver a very strong message that draws the patients away from our competitors and to us. I have included a word document generally outlining some of my requirements and thoughts, please review prior to investing time into design!

Target Market(s)

people who suffer from sleep apnea, which is a disease that causes them to stop breathing many times per hour, resulting in the patient needing to wear a device called a CPAP Machine. This is an illness that can impact anyone but is more likely to impact those suffering from obesity and men.

Industry/Entity Type

Health Care

Other font styles liked:
• Use what you think is best

Colors

Designer to choose colors to be used in the design.

Requirements
Must have
• Please see word document for must have items, and feel free to contact me with any questions.
• Also must have bold colors, and/or graphics to really stand out among my competitors brochures.
Nice to have
• Would prefer to use the baby picture titled "sleeping baby 4" if possible but provided 2 other baby photos just in case. Whatever you want to add, use your professional creativity! You Don't need to use all the pictures uploaded!!!!!
Should not have
• Nothing discriminatory or offensive.

```html
<!DOCTYPE html>
<html lang="en">
<head>
<meta charset="utf-8">
<title>RestWell Supply – Trifold Brochure</title>
<link href="https://fonts.googleapis.com/css2?family=Open+Sans:wght@300;400;600;700;800&display=swap" rel="stylesheet">
<style>
:root{
  --purple:#6e2a86;
  --purple-dark:#5a1f70;
  --green:#1e9a52;
  --green-light:#49b873;
  --ink:#333;
  --grey-panel:#eeeeef;
  --white:#fff;
  --gold:#e7a72a;
  --stage:#e4e4e4;
}
*{box-sizing:border-box;margin:0;padding:0}
html,body{width:806px;height:1200px;overflow:hidden;background:var(--stage);font-family:"Open Sans",Arial,sans-serif;color:var(--ink)}
.brochure{position:absolute;left:0;top:0;width:857px;height:660px;transform-origin:0 0;
  transform:translate(23px,307px) scale(0.887);background:var(--white);overflow:hidden;
  box-shadow:0 6px 18px rgba(0,0,0,.25)}
.panel{position:absolute;top:0;height:660px;width:286px}
.panel--left{left:0;background:var(--white)}
.panel--middle{left:286px;background:var(--grey-panel)}
.panel--right{left:572px;width:285px;background:#f4f4f6}
.waves{position:absolute;left:0;top:0}
.fold{position:absolute;top:0;width:1px;height:660px;background:rgba(0,0,0,.06)}
.txt{position:absolute}
.intro{left:22px;top:30px;width:250px;font-size:10px;line-height:13px}
.intro b{color:var(--purple)}
.how-title{left:24px;top:94px;font-size:23px;font-weight:800;color:var(--purple)}
.how-sub{left:24px;top:126px;font-size:9px;font-weight:600;letter-spacing:-.1px}
.benefits{left:22px;top:160px;width:250px;list-style:none}
.benefits li{position:relative;padding-left:22px;font-size:9.5px;line-height:13px;margin-bottom:13px}
.benefits li b{color:var(--green)}
.benefits svg{position:absolute;left:0;top:1px}
.left-cta{left:0;width:286px;top:558px;text-align:center;color:var(--white);font-size:14.5px;line-height:21px;font-weight:400}
.left-cta b{font-weight:700}
.left-cta .personal{display:block;margin-top:14px;font-size:17.5px}
.mid-head{left:286px;width:286px;top:28px;text-align:center;font-size:17px;font-weight:800;line-height:22px;color:var(--purple)}
.mid-head .g{color:var(--green)}
.mid-sub{left:286px;width:286px;top:74px;text-align:center;font-size:12px;font-weight:300}
.photo-ring{position:absolute;left:326px;top:95px}
.guarantee{left:286px;width:286px;top:303px;text-align:center;font-size:12.5px;line-height:16px}
.guarantee b{color:var(--purple)}
.seal{position:absolute;left:398px;top:342px;width:62px;height:62px;border-radius:50%;
  background:radial-gradient(circle at 40% 35%,#f7d35c 0,#e7a72a 70%,#c98a1a 100%)}
.pill{position:absolute;left:341px;top:519px;width:176px;height:34px;border-radius:17px;background:var(--white);text-align:center;
  box-shadow:0 1px 3px rgba(0,0,0,.3)}
.pill strong{display:block;font-size:12.5px;color:var(--purple);margin-top:3px;line-height:15px}
.pill span{display:block;font-size:7.5px;line-height:9px}
.contact{color:var(--white);text-align:center}
.mid-address{left:286px;width:286px;top:560px;font-size:9.5px;line-height:13px}
.mid-phone{left:286px;width:286px;top:597px;font-size:12.5px;font-weight:700;line-height:16px}
.mid-web{left:286px;width:286px;top:613px;font-size:12.5px;line-height:16px}
.tagline-bar{position:absolute;height:1px;background:rgba(255,255,255,.5)}
.mid-tag{left:286px;width:286px;top:637px;font-size:9.5px;letter-spacing:.2px;color:rgba(255,255,255,.85)}
.baby-photo{position:absolute;left:572px;top:0;width:285px;height:395px;
  background:radial-gradient(ellipse 75% 45% at 62% 52%,#edd3c2 0,#f0e2d9 40%,#f4f3f6 70%,#fbfbfc 100%)}
.right-head{left:572px;width:285px;top:24px;text-align:center;color:var(--purple);font-size:21px;line-height:25px;font-weight:300}
.right-head b{color:var(--green);font-weight:800}
.right-head .bold{font-weight:800}
.right-head small{display:block;font-size:13.5px;color:#333;font-weight:400;line-height:20px}
.right-head small b{color:var(--green)}
.brand{left:572px;width:285px;top:312px;text-align:center;font-size:25px;font-weight:400;color:var(--purple)}
.diff-head{left:572px;width:285px;top:430px;text-align:center;color:var(--white);font-size:14px;line-height:20px}
.diff-head b{font-weight:800}
.feature{position:absolute;top:475px;width:90px;text-align:center;color:var(--white);font-size:9px;font-weight:700}
.feature svg{display:block;margin:0 auto 4px}
.feature-divider{position:absolute;left:724px;top:478px;width:1px;height:38px;background:rgba(255,255,255,.5)}
.diff-list{left:572px;width:285px;top:530px;text-align:center;color:var(--white);font-size:9.5px;line-height:14px}
.right-tag{left:572px;width:285px;top:597px;font-size:10.5px;color:rgba(255,255,255,.85)}
.right-phone{left:572px;width:285px;top:618px;font-size:12.5px;font-weight:700;line-height:16px}
.right-serve{left:572px;width:285px;top:635px;font-size:10.5px;font-weight:600;line-height:14px}
</style>
</head>
<body>
<div class="brochure">
  <div class="panel panel--left"></div>
  <div class="panel panel--middle"></div>
  <div class="panel panel--right"></div>
  <div class="baby-photo" role="img" aria-label="Photo of a smiling baby sleeping on soft white bedding"></div>

  <svg class="waves" width="857" height="660" viewBox="0 0 857 660" aria-hidden="true">
    <path d="M0 438 C90 470 170 510 300 470 C430 430 520 385 640 372 C730 364 800 378 857 408 L857 660 L0 660 Z" fill="#49b873"/>
    <path d="M0 446 C90 482 170 522 300 482 C430 442 520 398 640 386 C730 378 800 392 857 422 L857 660 L0 660 Z" fill="#fff"/>
    <path d="M0 452 C90 490 170 530 300 490 C430 450 520 408 640 396 C730 388 800 402 857 432 L857 660 L0 660 Z" fill="#6e2a86"/>
  </svg>
  <div class="fold" style="left:286px"></div>
  <div class="fold" style="left:572px"></div>

  <p class="txt intro">Anyone can give you <b>CPAP</b> Supplies. However we are committed to providing you with exceptional customer service too.</p>
  <h2 class="txt how-title">How do we do this?</h2>
  <p class="txt how-sub">By giving you services no other CPAP retailer offers, like...</p>
  <ul class="txt benefits">
    <li><svg width="11" height="11" viewBox="0 0 11 11"><circle cx="5.5" cy="5.5" r="4.6" fill="none" stroke="#6e2a86" stroke-width="1.2"/><path d="M3 5.5l2 2 4-5" fill="none" stroke="#6e2a86" stroke-width="1.3"/></svg><b>Free Home Visits:</b> We bring the store to you so we can give you as much time you need and set up all you equipment and supplies for you.</li>
    <li><svg width="11" height="11" viewBox="0 0 11 11"><circle cx="5.5" cy="5.5" r="4.6" fill="none" stroke="#6e2a86" stroke-width="1.2"/><path d="M3 5.5l2 2 4-5" fill="none" stroke="#6e2a86" stroke-width="1.3"/></svg><b>Free Delivery:</b> So you never need to come to the store (Unless you want to!).</li>
    <li><svg width="11" height="11" viewBox="0 0 11 11"><circle cx="5.5" cy="5.5" r="4.6" fill="none" stroke="#6e2a86" stroke-width="1.2"/><path d="M3 5.5l2 2 4-5" fill="none" stroke="#6e2a86" stroke-width="1.3"/></svg>Night and Weekend Appointments: Because not everyone works 9-to-5.</li>
    <li><svg width="11" height="11" viewBox="0 0 11 11"><circle cx="5.5" cy="5.5" r="4.6" fill="none" stroke="#6e2a86" stroke-width="1.2"/><path d="M3 5.5l2 2 4-5" fill="none" stroke="#6e2a86" stroke-width="1.3"/></svg>A Dedicated Clinician: Because we also want to be your friend.</li>
    <li><svg width="11" height="11" viewBox="0 0 11 11"><circle cx="5.5" cy="5.5" r="4.6" fill="none" stroke="#6e2a86" stroke-width="1.2"/><path d="M3 5.5l2 2 4-5" fill="none" stroke="#6e2a86" stroke-width="1.3"/></svg>Hardship and Financial-assistance Programs: To make sure everyone gets the care they need.</li>
    <li><svg width="11" height="11" viewBox="0 0 11 11"><circle cx="5.5" cy="5.5" r="4.6" fill="none" stroke="#6e2a86" stroke-width="1.2"/><path d="M3 5.5l2 2 4-5" fill="none" stroke="#6e2a86" stroke-width="1.3"/></svg>Promise of Guaranteed Success: We offer 30-day guarantees on all supplies so you know you are getting the best care possible.</li>
  </ul>
  <p class="txt left-cta">Why are <b>YOU</b> Settling for <b>LESS?</b><br>Let US treat you <b>RIGHT!</b><span class="personal">We Make <b>CPAP Personal!</b></span></p>

  <h2 class="txt mid-head">CPAP <span class="g">DOESN'T NEED TO BE</span><br>LIKE THIS!</h2>
  <p class="txt mid-sub">Let us make sure this doesn't happen to you</p>
  <svg class="photo-ring" width="204" height="190" viewBox="0 0 204 190">
    <circle cx="102" cy="95" r="80" fill="#d9dde2" role="img" aria-label="Photo of a couple in bed, the man wearing a CPAP mask"/>
    <path d="M32 62 A88 88 0 0 1 102 7" fill="none" stroke="#1e9a52" stroke-width="7"/>
    <path d="M102 7 A88 88 0 0 1 178 62" fill="none" stroke="#6e2a86" stroke-width="7"/>
    <path d="M190 95 A88 88 0 0 1 102 183" fill="none" stroke="#1e9a52" stroke-width="7"/>
    <path d="M102 183 A88 88 0 0 1 14 95" fill="none" stroke="#6e2a86" stroke-width="7"/>
  </svg>
  <p class="txt guarantee">We Guarantee Your <b>CPAP Success,</b><br>because your Success is our Reputation</p>
  <div class="seal" role="img" aria-label="Satisfaction guarantee seal"></div>
  <div class="pill"><strong>Call For An Appointment</strong><span>(Or just to talk) Today</span></div>
  <p class="txt contact mid-address"><svg width="9" height="11" viewBox="0 0 9 11"><path d="M4.5 0a4 4 0 0 1 4 4c0 3-4 7-4 7S.5 7 .5 4a4 4 0 0 1 4-4z" fill="#49b873"/><circle cx="4.5" cy="4" r="1.5" fill="#6e2a86"/></svg> 48 Maple Row Lakeview,<br>Ontario L0S 1A0 Serving all of Ontario</p>
  <p class="txt contact mid-phone"><svg width="11" height="11" viewBox="0 0 11 11"><path d="M2 0.5l2 2.2-1 1.4c.8 1.6 2 2.8 3.6 3.6l1.4-1 2.2 2-1.2 1.8C4.8 10.2.8 6.2.3 1.8z" fill="#49b873"/></svg> 555-014-2290</p>
  <p class="txt contact mid-web"><svg width="10" height="10" viewBox="0 0 10 10"><circle cx="5" cy="5" r="4.5" fill="#49b873"/></svg> www.RestWellSupply.com</p>
  <div class="tagline-bar" style="left:336px;top:632px;width:186px"></div>
  <p class="txt contact mid-tag">WE BRING THE STORE TO YOU</p>

  <h1 class="txt right-head">WANT TO <b>SLEEP</b><br><span class="bold">LIKE A BABY AGAIN?</span><small>LET US SHOW <b>YOU HOW!</b></small></h1>
  <p class="txt brand">RestWell Supply</p>
  <p class="txt diff-head">WHAT MAKES US DIFFERENT?<br><b>EVERYTHING!</b></p>
  <div class="feature" style="left:632px">
    <svg width="24" height="24" viewBox="0 0 24 24"><circle cx="12" cy="12" r="12" fill="#49b873"/><path d="M6 12l6-5 6 5v6H6z" fill="#fff"/></svg>Free Home Visits</div>
  <div class="feature-divider"></div>
  <div class="feature" style="left:730px">
    <svg width="24" height="24" viewBox="0 0 24 24"><circle cx="12" cy="12" r="12" fill="#49b873"/><rect x="5" y="8" width="9" height="7" fill="#fff"/><path d="M14 10h3l2 3v2h-5z" fill="#fff"/><circle cx="8" cy="16" r="1.6" fill="#fff"/><circle cx="16" cy="16" r="1.6" fill="#fff"/></svg>Free delivery</div>
  <p class="txt diff-list">Night and weekend appointments<br>We specialize exclusively in Sleep Therapy<br>A dedicated clinician assigned directly to you<br>Hardship and financial-assistance programs</p>
  <div class="tagline-bar" style="left:612px;top:592px;width:205px"></div>
  <p class="txt contact right-tag">WE BRING THE STORE TO YOU</p>
  <div class="tagline-bar" style="left:612px;top:612px;width:205px"></div>
  <p class="txt contact right-phone"><svg width="11" height="11" viewBox="0 0 11 11"><path d="M2 0.5l2 2.2-1 1.4c.8 1.6 2 2.8 3.6 3.6l1.4-1 2.2 2-1.2 1.8C4.8 10.2.8 6.2.3 1.8z" fill="#49b873"/></svg> 555-014-2290</p>
  <p class="txt contact right-serve">Serving all of Ontario- www.RestWellSupply.com</p>
</div>
</body>
</html>
```